New Business Card Design Project

Need a design that will create an impact / strong impression towards our clients for our business. We are in the lighting business and we do lighting retrofits for large commercial to industrial clientele.

Target Market(s)

Lighting Industry

Industry/Entity Type

Business

Font styles to use
Other font styles liked:
• we would like to use the font on our logo, not sure what it is though..

Requirements
Must have
• Our logo.
Nice to have
• We are open to suggestions that have to do with lighting.

```html
<!DOCTYPE html>
<html lang="en">
<head>
<meta charset="utf-8">
<title>Lumera Retrofit Group – Business Card</title>
<link href="https://fonts.googleapis.com/css2?family=Montserrat:wght@400;500;600&display=swap" rel="stylesheet">
<style>
  :root {
    --backdrop: #2b2b2b;
    --green-deep: #0b4a1e;
    --green-mid: #0f7a3c;
    --green-bright: #6cc25a;
    --green-dark: #1f3d1c;
    --paper: #ffffff;
    --ink-grey: #7a7a7a;
  }
  * { margin: 0; padding: 0; box-sizing: border-box; }
  html, body { width: 1200px; height: 930px; overflow: hidden; }
  body {
    background: var(--backdrop);
    font-family: "Montserrat", sans-serif;
    position: relative;
  }
  .card {
    position: absolute;
    width: 560px;
    height: 320px;
    box-shadow: 0 18px 40px rgba(0,0,0,0.45);
    overflow: hidden;
  }
  /* Front side */
  .card--front {
    left: 90px;
    top: 90px;
    background: linear-gradient(160deg, #17602b 0%, var(--green-deep) 70%, #0a3f19 100%);
  }
  .card--front .surface {
    position: absolute; inset: 0;
    background: radial-gradient(ellipse at 60% 40%, rgba(255,255,255,0.06), transparent 65%);
  }
  .front-brand {
    position: absolute;
    left: 0; right: 0; top: 118px;
    text-align: center;
  }
  .brand-name {
    font-weight: 600;
    font-size: 30px;
    letter-spacing: 1px;
    display: inline-flex;
    align-items: center;
    gap: 10px;
  }
  .brand-mark {
    width: 14px; height: 14px;
    display: inline-block;
  }
  .card--front .brand-name { color: var(--paper); }
  .card--front .brand-mark { background: var(--green-bright); }
  .brand-rule {
    width: 300px; height: 1px;
    margin: 8px auto 6px;
    background: rgba(255,255,255,0.4);
  }
  .brand-tag {
    font-size: 11px;
    font-weight: 500;
    letter-spacing: 1.5px;
    color: var(--paper);
    text-transform: uppercase;
  }
  .front-web {
    position: absolute;
    left: 0; right: 0; bottom: 46px;
    text-align: center;
    font-size: 13px;
    letter-spacing: 1.5px;
    color: #d8e8d8;
  }
  .front-web span { color: var(--green-bright); }

  /* Back side */
  .card--back {
    left: 550px;
    top: 470px;
    background: var(--paper);
  }
  .back-brand {
    position: absolute;
    right: 30px; top: 30px;
    text-align: right;
  }
  .card--back .brand-name { color: var(--green-mid); font-size: 26px; }
  .card--back .brand-mark { background: var(--green-dark); }
  .card--back .brand-rule { width: 260px; margin: 6px 0 5px auto; background: var(--green-mid); }
  .card--back .brand-tag { color: var(--green-dark); font-size: 9.5px; }

  .person { position: absolute; left: 32px; top: 110px; }
  .person-name {
    font-size: 20px; font-weight: 500;
    color: var(--green-mid); text-transform: uppercase; letter-spacing: 0.5px;
  }
  .person-role { font-size: 15px; color: var(--ink-grey); }

  .address {
    position: absolute; left: 32px; top: 176px;
    font-size: 13px; line-height: 1.45; color: var(--ink-grey);
  }
  .contacts {
    position: absolute; left: 32px; bottom: 24px;
    list-style: none;
    font-size: 13px; color: var(--ink-grey); line-height: 1.6;
  }
  .contacts li { display: flex; align-items: center; gap: 10px; }
  .contacts svg { width: 11px; height: 11px; fill: var(--green-mid); }

  .corner-band {
    position: absolute; right: 0; top: 150px; bottom: 0; width: 150px;
    background: linear-gradient(135deg, var(--green-bright), var(--green-mid) 55%, var(--green-dark));
    clip-path: polygon(100% 0, 100% 100%, 0 100%);
  }
</style>
</head>
<body>

  <section class="card card--front">
    <div class="surface" role="img" aria-label="Soft green backdrop with faint perspective lines"></div>
    <div class="front-brand">
      <div class="brand-name"><span class="brand-mark"></span>LUMERA</div>
      <div class="brand-rule"></div>
      <div class="brand-tag">Lumera Retrofit Group, LLC.</div>
    </div>
    <div class="front-web">www.<span>lumeraretrofit</span>.com</div>
  </section>

  <section class="card card--back">
    <div class="back-brand">
      <div class="brand-name"><span class="brand-mark"></span>LUMERA</div>
      <div class="brand-rule"></div>
      <div class="brand-tag">Lumera Retrofit Group, LLC.</div>
    </div>

    <div class="person">
      <div class="person-name">Daniel Reyes</div>
      <div class="person-role">Founder</div>
    </div>

    <address class="address" style="font-style:normal">
      4870 Canyon Road,<br>Suite Mesa 85201
    </address>

    <ul class="contacts">
      <li><svg viewBox="0 0 24 24"><path d="M6.6 10.8a15 15 0 0 0 6.6 6.6l2.2-2.2c.3-.3.7-.4 1-.2 1.1.4 2.3.6 3.6.6.6 0 1 .4 1 1V20c0 .6-.4 1-1 1A17 17 0 0 1 3 4c0-.6.4-1 1-1h3.5c.6 0 1 .4 1 1 0 1.3.2 2.5.6 3.6.1.3 0 .7-.2 1z"/></svg>0400 555 019</li>
      <li><svg viewBox="0 0 24 24"><path d="M2 5h20v14H2z M2 5l10 8 10-8" /></svg>info@lumeraretrofit.com</li>
      <li><svg viewBox="0 0 24 24"><circle cx="12" cy="12" r="10"/></svg>www.lumeraretrofit.com</li>
    </ul>

    <div class="corner-band"></div>
  </section>

</body>
</html>
```